Meadowrun Acres Website Design

We have been redeveloping our website already and are quite happy with the content, but the design needs to be better:
https://tilvexa-hub.examplehost.net/

Pages, content, concept etc. Can all be taken from the redeveloped website.
The farmer can register and edit/view their profile, subscribe and these pages need to be designed better as well as contact, about, pricing, tos, privacy and a page with example portlets.

We need a website to appeal to farmers, investors and retiring farmers.

The design should be clean and a little country.

We don't want any repeat designs that some may submit to every project and has no respect for the project brief, so please don't submit them.

Target Market(s)

farmers, investors, retirees

Industry/Entity Type

Farming

Number of Pages Required

5+ page

Colors

Designer to choose colors to be used in the design.

Requirements
Must have
• Nice, clean modern design that is appealing
• Profile page laid out nicely

```html
<!DOCTYPE html>
<html lang="en">
<head>
<meta charset="utf-8">
<title>Investors | Meadowrun Acres</title>
<link rel="stylesheet" href="https://fonts.googleapis.com/css2?family=Questrial&family=Roboto:wght@400;500;700&display=swap">
<style>
:root{
  --green:#3aa935;
  --green-dark:#2d8a29;
  --orange:#f7861c;
  --ink:#222;
  --text:#555;
  --muted:#777;
  --rule:#e2e2e2;
  --light:#f2f2f2;
  --footer:#3b3b3b;
  --footer-bar:#2f2f2f;
  --white:#fff;
}
*{box-sizing:border-box;margin:0;padding:0}
html,body{width:1200px;height:3863px;overflow:hidden;background:var(--white)}
body{font-family:'Roboto',sans-serif;color:var(--text);position:relative}
a{text-decoration:none}

/* header */
.site-header{position:absolute;left:0;top:0;width:1200px;height:95px;background:var(--white);z-index:3}
.brand{position:absolute;left:77px;top:0;width:129px;height:124px;background:var(--white);border-bottom:4px solid var(--green);display:flex;flex-direction:column;align-items:center;justify-content:center;gap:8px}
.brand-dot{width:34px;height:34px;border-radius:50%;background:var(--green)}
.brand-name{font-family:'Roboto',sans-serif;font-weight:700;font-size:14px;color:var(--green);text-align:center;line-height:1.2}
.main-nav{position:absolute;left:227px;top:36px;display:flex;gap:22px}
.main-nav a{font-size:14px;font-weight:700;color:#444;letter-spacing:.2px;padding-bottom:6px}
.main-nav a.active{color:var(--green);border-bottom:3px solid var(--green)}
.account-link{position:absolute;left:945px;top:36px;font-size:14px;font-weight:700;color:var(--orange);display:flex;align-items:center;gap:8px}

/* hero */
.hero{position:absolute;left:0;top:95px;width:1200px;height:253px;background:linear-gradient(90deg,#3e4a34 0%,#5b6a48 35%,#6f7a58 60%,#4a5a3a 100%)}
.hero::after{content:"";position:absolute;inset:0;background:rgba(0,0,0,.35)}
.hero-title{position:absolute;left:0;width:1200px;top:102px;text-align:center;font-family:'Questrial',sans-serif;font-size:40px;color:var(--white);z-index:1}
.breadcrumb{position:absolute;left:0;top:348px;width:1200px;height:43px;background:var(--light);font-size:14px;color:#555;padding:12px 72px}
.breadcrumb a{color:var(--green)}

/* intro */
.intro-card{position:absolute;left:77px;top:435px;width:508px;height:338px;border:8px solid var(--green);padding:6px}
.intro-card-inner{position:relative;width:100%;height:100%;border:1px solid #9fd39c;padding:58px 26px 0;text-align:center;font-size:16px;line-height:1.55;color:#444}
.intro-card-inner p+p{margin-top:24px}
.btn{display:inline-block;background:var(--orange);color:var(--white);font-weight:700;text-transform:uppercase;text-align:center;border-radius:3px}
.btn-signup{position:absolute;left:26px;right:26px;top:262px;height:42px;line-height:42px;font-size:17px}
.video-back{position:absolute;left:623px;top:453px;width:510px;height:324px;background:var(--green)}
.video{position:absolute;left:613px;top:443px;width:510px;height:324px;background:radial-gradient(ellipse at 45% 40%,#6b5a4c 0%,#3a332d 45%,#1f1c1a 100%)}
.video-play{position:absolute;left:222px;top:130px}
.intro-copy{position:absolute;left:77px;top:815px;width:1050px;font-size:13.5px;line-height:1.6;color:#555}
.intro-copy p{margin-bottom:18px}

/* band */
.band{position:absolute;left:0;top:994px;width:1200px;height:494px;background:linear-gradient(180deg,#4c4f4c 0%,#5d6158 38%,#6e7a4c 62%,#4d5a36 100%)}
.band::after{content:"";position:absolute;inset:0;background:rgba(0,0,0,.22)}
.band-title{position:absolute;left:0;width:1200px;top:208px;text-align:center;font-family:'Questrial',sans-serif;font-weight:400;font-size:62px;color:var(--white);z-index:1}

/* benefits */
.section-title{position:absolute;left:0;width:1200px;text-align:center;font-family:'Roboto',sans-serif;font-weight:500;font-size:24px;color:var(--ink)}
.timeline-line{position:absolute;left:599px;top:1620px;width:2px;height:1110px;background:var(--rule)}
.node{position:absolute;left:561px;width:78px;height:78px;border-radius:50%;background:var(--white);border:3px solid #e4e4e4;display:flex;align-items:center;justify-content:center;box-shadow:0 0 0 6px #fafafa}
.benefit{position:absolute;width:468px}
.benefit h3{font-size:17px;font-weight:700;color:var(--ink);padding-bottom:10px;border-bottom:1px solid var(--rule)}
.benefit p{font-size:13px;color:#555;margin-top:8px;line-height:1.5}
.benefit.left{left:72px;text-align:right;padding-right:12px}
.benefit.left p{padding-left:60px}
.benefit.right{left:658px;text-align:left;padding-left:12px}
.benefit.right p{padding-right:40px}
.btn-enquire{position:absolute;left:533px;width:134px;height:40px;line-height:40px;font-size:13px}
.divider{position:absolute;left:72px;top:2871px;width:1055px;height:1px;background:var(--rule)}

/* expectations */
.exp-line{position:absolute;left:72px;top:3184px;width:1055px;height:3px;background:var(--green)}
.exp-node{position:absolute;top:3126px;width:118px;height:118px;border-radius:50%;background:var(--white);border:4px solid var(--green);box-shadow:0 0 0 8px #ececec;display:flex;align-items:center;justify-content:center}
.exp-label{position:absolute;width:200px;text-align:center}
.exp-label h3{font-size:17px;font-weight:700;color:var(--ink);margin-bottom:10px}
.exp-label p{font-size:13px;line-height:1.5;color:#555;padding:0 20px}

/* footer */
.site-footer{position:absolute;left:0;top:3523px;width:1200px;height:288px;background:var(--footer);color:#ddd}
.footer-heading{position:absolute;font-size:15px;font-weight:700;color:var(--white)}
.post{position:absolute;left:72px;display:flex;gap:14px;width:340px}
.post-date{width:57px;height:57px;background:var(--green);color:var(--white);text-align:center;flex:none}
.post-date b{display:block;font-size:26px;line-height:36px}
.post-date span{display:block;font-size:10px;background:var(--green-dark);line-height:21px}
.post h4{font-size:14px;color:var(--white);font-weight:700;line-height:1.3}
.post small{font-size:11px;color:#bbb}
.newsletter-copy{position:absolute;left:494px;top:3600px;font-size:13px;color:#ccc;width:340px;line-height:1.5}
.email-field{position:absolute;left:494px;top:3660px;width:335px;height:38px;background:var(--white);border-radius:19px;padding:0 18px;font-size:12px;color:#999;line-height:38px}
.btn-subscribe{position:absolute;left:494px;top:3703px;width:129px;height:36px;line-height:36px;font-size:14px;border-radius:18px;text-transform:none}
.footer-brand{position:absolute;left:914px;top:3580px;width:206px;text-align:center}
.footer-brand .brand-dot{margin:0 auto 22px;width:56px;height:56px;background:none;border:2px solid #ddd}
.footer-brand span{font-family:'Roboto',sans-serif;font-size:22px;color:#ddd}
.footer-bar{position:absolute;left:0;top:3811px;width:1200px;height:52px;background:var(--footer-bar);font-size:12px;color:#aaa;padding:18px 72px}
.social{position:absolute;right:75px;top:14px;display:flex;gap:8px}
.social i{display:block;width:26px;height:26px;border-radius:50%;background:#bbb}
</style>
</head>
<body>

<header class="site-header">
  <a class="brand" href="#"><span class="brand-dot"></span><span class="brand-name">Meadowrun<br>Acres</span></a>
  <nav class="main-nav">
    <a href="#">HOME</a>
    <a href="#">ASPIRING FARMERS</a>
    <a href="#" class="active">INVESTORS</a>
    <a href="#">RETIRING FARMER</a>
    <a href="#">BLOG</a>
    <a href="#">PRICING</a>
    <a href="#">CONTACT</a>
  </nav>
  <div class="account-link">
    <svg width="16" height="16" viewBox="0 0 16 16" fill="none" stroke="currentColor" stroke-width="1.8"><rect x="2" y="3" width="12" height="10" rx="1"/><path d="M5 7h6M5 10h4"/></svg>
    SIGN IN OR SIGN UP
  </div>
</header>

<section class="hero" role="img" aria-label="Photo of a young farming family with children standing in front of trees">
  <h1 class="hero-title">Investors</h1>
</section>
<div class="breadcrumb"><a href="#">Home</a> / Investors</div>

<div class="intro-card">
  <div class="intro-card-inner">
    <p>We have the best farmers in Australia ready to work with you on your farm.</p>
    <p>Simply browse the list and decide who you want to work with. No registration required and your information will be kept private.</p>
    <a href="#" class="btn btn-signup">Sign up now!</a>
  </div>
</div>
<div class="video-back"></div>
<div class="video" role="img" aria-label="Video still of a young farmer speaking on a verandah">
  <svg class="video-play" width="66" height="66" viewBox="0 0 66 66"><circle cx="33" cy="33" r="32" fill="rgba(255,255,255,.9)"/><path d="M26 20l20 13-20 13z" fill="#333"/></svg>
</div>

<div class="intro-copy">
  <p>If you're looking for a farm manager then we have the best from all over Australia them right here. Finding the best farmer can be a difficult task.</p>
  <p>We have these best aspiring farmers at our fingertips because we know what they want out of farming. We also know that anyone we match for you will be passionate and the best fit for your operation.</p>
  <p>Get in touch to find out more your information is completely confidential.</p>
</div>

<section class="band" role="img" aria-label="Photo of a rider on horseback herding black cattle in front of a farm shed">
  <h2 class="band-title">Find Your Farmer With Us</h2>
</section>

<h2 class="section-title" style="top:1538px">Benefits</h2>
<div class="timeline-line"></div>

<div class="node" style="top:1622px"><svg width="34" height="34" viewBox="0 0 34 34" fill="var(--green)"><path d="M17 3L3 10h28z"/><rect x="6" y="12" width="3" height="14"/><rect x="12" y="12" width="3" height="14"/><rect x="19" y="12" width="3" height="14"/><rect x="25" y="12" width="3" height="14"/><rect x="3" y="27" width="28" height="4"/></svg></div>
<div class="node" style="top:1735px"><svg width="34" height="34" viewBox="0 0 34 34" fill="var(--green)"><path d="M20 5l11 10-11 10v-6c-8 0-13 2-16 9 1-10 6-16 16-17z"/></svg></div>
<div class="node" style="top:1838px"><svg width="34" height="34" viewBox="0 0 34 34" fill="none" stroke="var(--green)" stroke-width="3"><path d="M4 4v26h26"/><path d="M8 24l7-8 5 5 9-10"/></svg></div>
<div class="node" style="top:1941px"><svg width="36" height="36" viewBox="0 0 36 36"><rect x="3" y="9" width="30" height="18" fill="var(--green)"/><rect x="7" y="13" width="22" height="10" fill="#fff"/><circle cx="18" cy="18" r="4" fill="var(--green)"/></svg></div>
<div class="node" style="top:2042px"><svg width="34" height="34" viewBox="0 0 34 34" fill="var(--green)"><path d="M15 4A13 13 0 1 0 28 19H15z"/><path d="M18 2v14h14A14 14 0 0 0 18 2z"/></svg></div>
<div class="node" style="top:2142px"><svg width="36" height="34" viewBox="0 0 36 34" fill="var(--green)"><circle cx="10" cy="9" r="5"/><circle cx="26" cy="9" r="5"/><circle cx="18" cy="13" r="5"/><path d="M2 26c0-6 4-10 8-10s6 2 6 4H2zM34 26c0-6-4-10-8-10s-6 2-6 4h14zM8 31c0-7 4-11 10-11s10 4 10 11z"/></svg></div>
<div class="node" style="top:2245px"><svg width="30" height="36" viewBox="0 0 30 36" fill="var(--green)"><circle cx="15" cy="5" r="4"/><path d="M2 10l13 3 13-3v4l-9 2v18h-4v-9h0v9h-4V16L2 14z"/></svg></div>
<div class="node" style="top:2345px"><svg width="30" height="34" viewBox="0 0 30 34"><path d="M8 15V10a7 7 0 0 1 14 0v5" fill="none" stroke="var(--green)" stroke-width="3"/><rect x="4" y="15" width="22" height="17" rx="2" fill="var(--green)"/></svg></div>
<div class="node" style="top:2448px"><svg width="36" height="34" viewBox="0 0 36 34" fill="var(--green)"><path d="M18 3L2 17h4v14h9v-9h6v9h9V17h4z"/></svg></div>
<div class="node" style="top:2549px"><svg width="38" height="32" viewBox="0 0 38 32" fill="var(--green)"><path d="M19 4L1 12l18 8 18-8z"/><path d="M8 16v8c4 4 18 4 22 0v-8l-11 5z"/><rect x="33" y="12" width="2" height="12"/></svg></div>
<div class="node" style="top:2652px"><svg width="32" height="34" viewBox="0 0 32 34"><path d="M18 15V9a6 6 0 0 1 12 0v3" fill="none" stroke="var(--green)" stroke-width="3"/><rect x="2" y="15" width="22" height="17" rx="2" fill="var(--green)"/></svg></div>

<div class="benefit left" style="top:1637px"><h3>Ownership</h3><p>Own your own farm without having to run it</p></div>
<div class="benefit right" style="top:1750px"><h3>Share</h3><p>Share the farm and it's operation with a passionate young family and retiring family.</p></div>
<div class="benefit left" style="top:1853px"><h3>Performance</h3><p>High quality investment – you are in control in deciding the farm establishment and management processes.</p></div>
<div class="benefit right" style="top:1956px"><h3>Return</h3><p>Receive an annual return on investment</p></div>
<div class="benefit left" style="top:2057px"><h3>Capital</h3><p>Realise capital returns upon exit</p></div>
<div class="benefit right" style="top:2157px"><h3>Participate</h3><p>Be a valued member of a regional community.</p></div>
<div class="benefit left" style="top:2260px"><h3>Choice</h3><p>Access to the best aspiring farmers across Australia.</p></div>
<div class="benefit right" style="top:2360px"><h3>Private</h3><p>Anonymous - your information will be kept private.</p></div>
<div class="benefit left" style="top:2463px"><h3>Stay</h3><p>Stay on your farm to enjoy the experience.</p></div>
<div class="benefit right" style="top:2564px"><h3>Learning</h3><p>Educate your children about farming</p></div>
<div class="benefit left" style="top:2667px"><h3>Farm opportunities</h3><p>Sit and discuss the best outcome for you, aspiring farmer and retiring farmer in the specific farm opportunity.</p></div>

<a href="#" class="btn btn-enquire" style="top:2787px">Enquire now</a>
<div class="divider"></div>

<h2 class="section-title" style="top:2913px">Expectations</h2>

<div class="exp-label" style="left:62px;top:2983px"><h3>Management</h3><p>Know you have a great farmer supported by great advisors</p></div>
<div class="exp-label" style="left:500px;top:2983px"><h3>Connect</h3><p>Connect with the farming family</p></div>
<div class="exp-label" style="left:938px;top:2983px"><h3>Promote</h3><p>Promote the produce to friends</p></div>

<div class="exp-line"></div>
<div class="exp-node" style="left:103px"><svg width="54" height="50" viewBox="0 0 34 32" fill="none" stroke="var(--green)" stroke-width="3"><path d="M3 3v26h28"/><path d="M7 23l7-8 5 5 9-10"/></svg></div>
<div class="exp-node" style="left:322px"><svg width="56" height="52" viewBox="0 0 36 34" fill="var(--green)"><circle cx="10" cy="9" r="5"/><circle cx="26" cy="9" r="5"/><circle cx="18" cy="13" r="5"/><path d="M2 26c0-6 4-10 8-10s6 2 6 4H2zM34 26c0-6-4-10-8-10s-6 2-6 4h14zM8 31c0-7 4-11 10-11s10 4 10 11z"/></svg></div>
<div class="exp-node" style="left:541px"><svg width="54" height="54" viewBox="0 0 36 36" fill="none" stroke="var(--green)" stroke-width="4"><rect x="4" y="12" width="16" height="10" rx="5" transform="rotate(45 12 17)"/><rect x="16" y="14" width="16" height="10" rx="5" transform="rotate(45 24 19)"/></svg></div>
<div class="exp-node" style="left:760px"><svg width="58" height="50" viewBox="0 0 38 32"><path d="M3 11h32l-4 18H7z" fill="var(--green)"/><path d="M10 11l6-8M28 11l-6-8" stroke="var(--green)" stroke-width="3"/><path d="M13 15v10M19 15v10M25 15v10" stroke="#fff" stroke-width="2"/></svg></div>
<div class="exp-node" style="left:979px"><svg width="50" height="56" viewBox="0 0 32 36" fill="var(--green)"><rect x="14" y="2" width="4" height="33"/><path d="M5 6h22l4 4-4 4H5z"/><path d="M27 17H7l-4 4 4 4h20z"/></svg></div>

<div class="exp-label" style="left:281px;top:3292px"><h3>Share</h3><p>Share the farming experience with your friends and family</p></div>
<div class="exp-label" style="left:719px;top:3292px"><h3>Produce</h3><p>Purchase produce</p></div>

<a href="#" class="btn btn-enquire" style="top:3425px">Enquire now</a>

<footer class="site-footer">
  <h4 class="footer-heading" style="left:72px;top:42px">From The Blog</h4>
  <h4 class="footer-heading" style="left:494px;top:42px">Subscribe To Our Newsletter</h4>
</footer>
<div class="post" style="top:3600px"><div class="post-date"><b>24</b><span>APR 17</span></div><div><h4>Out of the Waffle Cottage into the fire of soil health | Tom Ridley</h4><small>Posted by Tom Ridley</small></div></div>
<div class="post" style="top:3703px"><div class="post-date"><b>21</b><span>APR 17</span></div><div><h4>Harlow is a cool name, so is Tess, but their passion for farming</h4><small>Posted by Harlow and Tess</small></div></div>
<p class="newsletter-copy">Want to be the first to know about our amazing discount offer?</p>
<div class="email-field">Email Address</div>
<a href="#" class="btn btn-subscribe">Subscribe</a>
<div class="footer-brand"><div class="brand-dot"></div><span>Meadowrun Acres</span></div>
<div class="footer-bar">©2017 Meadowrun Acres. Terms of Use | Privacy | Sitemap | Donate
  <div class="social"><i></i><i></i><i></i></div>
</div>

</body>
</html>
```